SitePress Direct-Booking Website for Bend, Oregon Vacation Rental — $750 Budget
Project Overview

We are looking for a talented SitePress designer/developer to create a clean, professional and inviting direct-booking website for Birch Lantern Retreat, an established short-term vacation rental in Bend, Oregon.

The property is currently successfully listed on Staynest and Hoplo. Our Staynest property has approximately a 4.98-star rating with more than 200 reviews, is an Staynest Visitor Pick, and ranks among the Top 1% of eligible homes.

Project Budget: $750

We will select the designer based on the quality of the initial concept, understanding of the property, proposed booking solution and ability to deliver a completed and functioning SitePress website.

Existing Staynest Listing

Please use our current Staynest listing as the primary reference for photographs, property details, amenities and design inspiration:

https://www.staynest-example.net/rooms/48172036

Original high-resolution photographs and additional property information will be provided to the selected designer.

Design Direction

We want the website to feel:

Upscale but comfortable
Warm and welcoming
Clean and uncluttered
Pacific Northwest / Central Oregon
Professional rather than corporate
Highly visual with large property photographs
Easy to navigate
Excellent on phones, tablets and desktop computers

We welcome creativity and want designers to show us their vision for the property rather than simply copying our Staynest listing.

The website should immediately communicate that Birch Lantern Retreat is a highly rated vacation rental in an excellent Bend location.

Key Property Features
3 bedrooms
2 bathrooms
Sleeps up to 6 guests
Pet friendly
Approximately a 5-minute walk to Bend's Tannery Row Quarter
Near restaurants, shopping and Larkspur Fields Pavilion
Private fenced backyard
Covered outdoor area
Off-street driveway parking
Fireplace
Well-equipped kitchen
Staynest Prime Keeper
Staynest Visitor Pick
Top 1% of eligible Staynest homes
Approximately 4.98 stars with 200+ guest reviews

Our location, guest reviews, cleanliness, comfort, backyard, pet-friendly accommodations and walkability should be major selling points throughout the website.

Website Structure

We anticipate approximately 6–7 pages:

Home

Large hero photograph with a strong opening message and prominent BOOK DIRECT and CHECK AVAILABILITY buttons.

The home page should quickly communicate:

BIRCH LANTERN RETREAT — BEND, OREGON

3 Bedrooms | 2 Baths | Sleeps 6 | Pet Friendly | Walk to Tannery Row

Our exceptional guest rating and Staynest history should also be prominently featured.

The House

Bedrooms, bathrooms, kitchen, living areas, backyard and major amenities.

Photo Gallery

Large, attractive and fast-loading photographs with an easy-to-use mobile gallery.

Location / Explore Bend

Tannery Row Quarter, Larkspur Fields Pavilion, Deschutes River, restaurants, breweries, shopping, downtown Bend and nearby outdoor recreation.

Guest Reviews

Selected guest reviews and prominent presentation of our strong Staynest reputation.

Availability & Book Direct

A simple and professional direct-booking experience.

Contact / FAQ

Contact information plus common questions regarding pets, parking, check-in/check-out, cancellations and other policies.

IMPORTANT — Direct Booking & Credit Card Requirements

We want guests to be able to book directly through the website without having to contact us first.

The website should use a proven SitePress vacation-rental booking plugin or system rather than a custom-built reservation/payment system.

Guests should be able to:

Select arrival and departure dates
See available dates
Enter number of guests
See nightly charges
See cleaning fees
See applicable lodging taxes and other charges
See the complete reservation total before paying
Enter guest/contact information
Pay securely by credit or debit card
Receive an automatic reservation confirmation

Paywell is our preferred credit-card processor.

Credit-card information must be processed securely through Paywell or another established payment processor. Credit-card information should NOT be stored directly on our SitePress website.

Staynest & Hoplo Calendar Synchronization

This is very important.

The direct-booking calendar must synchronize with our existing Staynest and Hoplo calendars to reduce the possibility of double bookings.

For this single-property website, we prefer a simple solution using Staynest/Hoplo calendar or iCal synchronization rather than an expensive monthly channel-management service, if practical.

The designer should clearly identify the booking plugin/system they propose using.

IMPORTANT — Tell Us Your Proposed Booking Solution

As part of your submission, please tell us:

Which SitePress booking plugin/system you recommend.
Whether it synchronizes availability with Staynest and Hoplo.
Whether it integrates directly with Paywell.
The initial cost of the plugin/software.
Any annual or monthly fees.
Whether any additional paid software or services will be required.

We strongly prefer a solution with little or no ongoing monthly software expense.

We do not want to select a designer and later discover that the proposed booking system requires an expensive monthly subscription.

SitePress & Technical Requirements

The completed project should include:

Fully functioning SitePress website
Responsive desktop/tablet/mobile design
Fast-loading pages
Optimized photographs
SSL/HTTPS compatibility
Direct-booking functionality
Paywell payment integration
Staynest calendar synchronization
Hoplo calendar synchronization
Automatic booking confirmations
Cleaning fee and lodging-tax calculations
Contact form
Vizor Maps/location integration
Basic spam/security protection
Vizor Metrics capability
Basic SEO setup
Search-engine submission capability
Easy owner editing of text, rates and photographs
Search Engine Optimization

The website should be structured for Vizor and other search engines.

Important search themes include:

Bend Oregon vacation rental
Bend Oregon vacation home
Tannery Row Quarter vacation rental
Vacation rental near Tannery Row Bend
Bend Oregon pet-friendly vacation rental
Bend vacation rental near Larkspur Fields Pavilion
Bend Oregon direct booking vacation rental

We are not expecting an extensive ongoing SEO campaign for the $750 project. We do expect proper page titles, descriptions, headings, image optimization and a good technical foundation for future SEO.

Ownership

Upon completion and final payment:

We own the completed SitePress website.
We receive full SitePress administrator access.
We control the domain and hosting accounts.
We own all custom design files created for the project.
All necessary login credentials are provided to us.
The website can be moved to another SitePress hosting provider in the future.
There should be no proprietary dependency on the developer after completion.
What We Want From Contestants

Please review our Staynest listing before submitting your concept.

We are particularly interested in seeing an initial homepage concept showing how you would present:

Birch Lantern Retreat
The Bend / Tannery Row location
Our photography
Our exceptional guest reviews and ratings
The Book Direct message
The availability/booking call-to-action

We will provide feedback on the concepts we like and work with the selected designer to refine and complete the website.

Our Goal

Our objective is straightforward:

Create a beautiful, trustworthy and easy-to-use website that encourages guests to book Birch Lantern Retreat directly with us.

The website will complement—not replace—our existing Staynest and Hoplo listings.

We want repeat guests and new customers to have an easy way to find the property, check availability and book directly while receiving the same professional experience they expect from a major vacation-rental platform.

Target Market(s)

Consumers looking to to travel to Mexico for vacation. Family or couples

Industry/Entity Type

Short term vacation rental industry

Coding

Coded - Design and coding required

Number of Pages Required

5+ page

Requirements
Must have
• Capabilities to accept credit card payments and link to other rental property sites calendars such as HOPLO and Staynset
Nice to have
• Option for best plugins for property rental

```html
<!DOCTYPE html>
<html lang="en">
<head>
<meta charset="utf-8">
<title>Birch Lantern Retreat — Bend, Oregon Vacation Rental</title>
<link href="https://fonts.googleapis.com/css2?family=Montserrat:wght@400;500;600;700;800&family=Great+Vibes&display=swap" rel="stylesheet">
<style>
:root{
  --green:#4d6530;
  --green-dark:#3e5426;
  --olive:#9a8a40;
  --olive-band:#a18f42;
  --yellow:#f6e78c;
  --yellow-btn:#f7e27a;
  --black:#0b0b0b;
  --white:#ffffff;
  --ink:#2c2c2c;
}
*{box-sizing:border-box;margin:0;padding:0}
html,body{width:1200px;height:4357px;overflow:hidden}
body{position:relative;background:var(--white);font-family:'Montserrat',sans-serif;color:var(--ink)}
.abs{position:absolute}
.script{font-family:'Great Vibes',cursive;font-weight:400;line-height:1;white-space:nowrap}

/* Hero */
.hero-photo{left:0;top:0;width:1200px;height:505px;background:linear-gradient(180deg,#3d3a55 0%,#5c5468 30%,#6a5a4e 55%,#3b3526 80%,#2a2a1f 100%)}
.hero-shade{left:0;top:0;width:1200px;height:505px;background:linear-gradient(180deg,rgba(0,0,0,.35),rgba(0,0,0,.05) 60%,rgba(0,0,0,.25))}
.nav a{position:absolute;top:23px;color:var(--white);font-size:10px;font-weight:600;text-decoration:none;letter-spacing:.3px;transform:translateX(-50%)}
.nav .active{border-bottom:1px solid var(--yellow);padding:0 10px 9px}
.brand{left:600px;top:14px;transform:translateX(-50%);display:flex;align-items:center;gap:8px;color:var(--white);font-size:11px;font-weight:700;letter-spacing:.6px;white-space:nowrap}
.brand .dot{width:22px;height:22px;border:1.5px solid var(--white);border-radius:50%}
.btn-book{left:912px;top:12px;width:138px;height:34px;background:var(--yellow-btn);border-radius:17px;color:#1c1c1c;font-size:10px;font-weight:700;display:flex;align-items:center;justify-content:center}
.hero-kicker{left:0;width:1200px;top:118px;text-align:center;color:var(--white);font-size:10px;font-weight:700;letter-spacing:1px}
.hero-h1{left:0;width:1200px;top:140px;text-align:center;color:var(--white);font-weight:800;line-height:1}
.hero-h1 .l1{display:block;font-size:50px}
.hero-h1 .l2{display:block;font-size:34px;margin-top:2px}
.hero-script{left:0;width:1200px;top:228px;text-align:center;color:var(--yellow);font-size:44px}
.hero-facts{left:0;width:1200px;top:304px;display:flex;justify-content:center;gap:18px;color:var(--white);font-size:10px;font-weight:700}
.hero-facts span{display:flex;align-items:center;gap:6px}
.chev{left:588px;top:366px}
.cta{z-index:4;top:423px;height:37px;border-radius:19px;font-size:10px;font-weight:700;display:flex;align-items:center;justify-content:center;gap:6px}
.cta-direct{left:400px;width:196px;background:var(--yellow-btn);color:#1c1c1c}
.cta-avail{left:601px;width:195px;background:var(--green);color:var(--white)}
.stats{z-index:3;left:146px;top:444px;width:904px;height:132px;background:var(--black);border-radius:66px;display:flex;justify-content:center;align-items:center;gap:36px;padding-top:20px}
.stat{display:flex;align-items:center;gap:10px;color:var(--white)}
.stat .ring{width:50px;height:50px;border:1.5px solid var(--yellow);border-radius:50%;display:flex;align-items:center;justify-content:center}
.stat b{display:block;font-size:24px;font-weight:700;line-height:1}
.stat small{display:block;font-size:9px;font-weight:600;margin-top:3px}

/* Intro */
.intro-bg{left:0;top:505px;width:1200px;height:820px;background:linear-gradient(180deg,var(--yellow) 0%,var(--yellow) 70%,var(--white) 100%)}
.intro-h2{left:300px;width:274px;top:669px;text-align:right;color:var(--green);font-size:44px;font-weight:800;line-height:1}
.q-photo-tr{left:603px;top:640px;width:334px;height:334px;border-radius:0 100% 0 0;background:linear-gradient(160deg,#c9b88a,#8a7a58 50%,#6b6446)}
.q-photo-bl{left:268px;top:829px;width:335px;height:335px;border-radius:0 0 0 100%;background:linear-gradient(200deg,#b99a70,#8a5f3c 55%,#5b3d26)}
.intro-copy{left:630px;top:1006px;width:300px;font-size:10.5px;line-height:1.5;color:#222}
.intro-copy p+p{margin-top:14px}

/* Comfort */
.sec-h2{left:0;width:1200px;text-align:center;color:var(--green);font-size:38px;font-weight:800;line-height:1.05}
.sec-script{left:0;width:1200px;text-align:center;color:var(--green);font-size:42px}
.vline{left:599px;width:1px;height:50px;background:#8a8a8a}
.yard-photo{left:0;top:1720px;width:1200px;height:760px;background:linear-gradient(180deg,#ffffff 0%,#cfd8c4 14%,#7a8f6a 38%,#4f7a32 65%,#3f6a26 100%)}
.card{position:absolute;width:266px;height:244px;border-radius:27px;color:var(--white);text-align:center;padding-top:52px}
.card.green{background:var(--green)}
.card.olive{background:var(--olive)}
.card .ico{width:64px;height:64px;border-radius:50%;margin:0 auto 12px;display:flex;align-items:center;justify-content:center}
.card.green .ico{background:#bfe08f}
.card.olive .ico{background:#3f4a26}
.card h3{font-size:11px;font-weight:700;line-height:1.35}
.card p{font-size:10px;line-height:1.35;margin:6px auto 0;width:210px}
.yard-notch{left:95px;top:2478px;width:1010px;height:80px;background:#3f6a26;clip-path:polygon(0 0,100% 0,94% 100%,6% 100%)}
.gal{top:2480px;width:219px;height:251px;border-radius:30px}

/* Adventure */
.adv-h2{left:180px;width:390px;top:2878px;text-align:center;color:var(--green);font-size:40px;font-weight:800;line-height:.95}
.adv-script{left:160px;width:430px;top:2952px;text-align:center;color:var(--green);font-size:42px}
.adv-copy{left:200px;width:350px;top:3019px;text-align:center;font-size:10.5px;line-height:1.45}
.btn-explore{left:288px;top:3063px;width:195px;height:36px;border-radius:18px;background:var(--green);color:var(--white);font-size:10px;font-weight:700;display:flex;align-items:center;justify-content:center;gap:6px}
.spot{top:2856px;width:219px;height:251px;border-radius:30px}
.spot-cap{z-index:2;top:3120px;width:219px;text-align:center;color:var(--green);font-size:11px;font-weight:700;line-height:1.3}
.spot-cap span{display:block;font-weight:500;color:#555}
.river-photo{left:0;top:3170px;width:1200px;height:343px;background:linear-gradient(180deg,#ffffff 0%,#c2c7b4 12%,#7f8a6c 35%,#4c6b5c 60%,#3c5a38 100%)}

/* Reviews */
.review{top:3694px;width:324px;height:298px;background:var(--green);border-radius:0 90px 0 0;color:var(--white);padding:42px 36px 0 68px}
.review h4{font-size:19px;font-weight:600}
.review .stars{color:var(--yellow);font-size:11px;letter-spacing:1px;margin-top:2px}
.review p{font-size:10.5px;line-height:1.5;margin-top:10px}
.avatar{top:3793px;width:100px;height:100px;border-radius:50%;background:linear-gradient(135deg,#b98a6a,#5a3f30)}
.arrow{top:3820px}

/* Newsletter */
.news{left:0;top:4072px;width:1200px;height:211px;background:var(--olive-band)}
.news h2{position:absolute;left:0;width:1200px;top:46px;text-align:center;color:var(--white);font-size:29px;font-weight:700}
.news .sub{position:absolute;left:0;width:1200px;top:84px;text-align:center;color:var(--white);font-size:10.5px}
.field{top:120px;height:37px;border:1.5px solid var(--white);border-radius:19px;color:var(--white);font-size:10px;font-weight:700;padding:13px 0 0 18px}
.btn-sub{left:760px;top:120px;width:137px;height:37px;border-radius:19px;background:var(--green);color:var(--white);font-size:10px;font-weight:700;display:flex;align-items:center;justify-content:center;gap:6px}

/* Footer */
.footer{left:0;top:4283px;width:1200px;height:74px;background:var(--black);color:var(--white)}
.footer nav{position:absolute;top:30px;left:0;width:1200px;text-align:center;font-size:9.5px;font-weight:700}
.footer nav span{margin:0 8px}
.footer small{position:absolute;top:52px;left:0;width:1200px;text-align:center;font-size:9px;color:#ccc}
</style>
</head>
<body>

<!-- HERO -->
<div class="abs hero-photo" role="img" aria-label="Twilight view over Bend, Oregon with city lights and the river"></div>
<div class="abs hero-shade"></div>
<nav class="nav">
  <a class="active" style="left:211px">HOME</a>
  <a style="left:278px">THE HOUSE</a>
  <a style="left:351px">GALLERY</a>
  <a style="left:434px">EXPLORE BEND</a>
  <a style="left:755px">REVIEWS</a>
  <a style="left:811px">FAQ</a>
  <a style="left:865px">CONTACT</a>
</nav>
<div class="abs brand"><span class="dot"></span>BIRCH LANTERN RETREAT</div>
<div class="abs btn-book">BOOK DIRECT</div>

<div class="abs hero-kicker">BIRCH LANTERN RETREAT BEND, &nbsp;OREGON</div>
<h1 class="abs hero-h1"><span class="l1">YOUR CHARMING</span><span class="l2">BEND GETAWAY</span></h1>
<div class="abs hero-script script">Steps from the Tannery Row Quarter</div>
<div class="abs hero-facts">
  <span><svg width="16" height="12" viewBox="0 0 16 12"><rect x="1" y="5" width="14" height="5" fill="#fff"/><rect x="1" y="1" width="2" height="10" fill="#fff"/><rect x="4" y="3" width="5" height="3" fill="#fff"/></svg>3 BEDROOMS</span>
  <span><svg width="16" height="12" viewBox="0 0 16 12"><rect x="1" y="6" width="14" height="4" rx="1" fill="#fff"/><rect x="2" y="1" width="2" height="6" fill="#fff"/></svg>2 BATHS</span>
  <span><svg width="18" height="12" viewBox="0 0 18 12"><circle cx="5" cy="3" r="2.5" fill="#fff"/><circle cx="13" cy="3" r="2.5" fill="#fff"/><circle cx="9" cy="4" r="2.5" fill="#fff"/><rect x="1" y="7" width="16" height="5" rx="2.5" fill="#fff"/></svg>SLEEPS 6</span>
  <span><svg width="14" height="12" viewBox="0 0 14 12"><circle cx="7" cy="8" r="3.5" fill="#fff"/><circle cx="2.5" cy="4.5" r="1.6" fill="#fff"/><circle cx="11.5" cy="4.5" r="1.6" fill="#fff"/><circle cx="5" cy="1.8" r="1.6" fill="#fff"/><circle cx="9" cy="1.8" r="1.6" fill="#fff"/></svg>PET FRIENDLY</span>
</div>
<svg class="abs chev" width="24" height="26" viewBox="0 0 24 26"><path d="M3 3l9 8 9-8M3 13l9 8 9-8" fill="none" stroke="#fff" stroke-width="2"/></svg>

<!-- INTRO BACKGROUND -->
<div class="abs intro-bg"></div>

<!-- STATS BAR -->
<div class="abs stats">
  <div class="stat"><div class="ring"><svg width="22" height="22" viewBox="0 0 22 22"><circle cx="11" cy="8" r="4" fill="none" stroke="#f6e78c" stroke-width="1.6"/><path d="M4 19c1-4 4-6 7-6s6 2 7 6" fill="none" stroke="#f6e78c" stroke-width="1.6"/></svg></div><div><b>4.98</b><small>Guest Rating</small></div></div>
  <div class="stat"><div class="ring"><svg width="22" height="22" viewBox="0 0 22 22"><path d="M11 2l2.7 5.6 6.1.8-4.5 4.2 1.1 6.1L11 15.8 5.6 18.7l1.1-6.1L2.2 8.4l6.1-.8z" fill="#f6e78c"/></svg></div><div><b>200+</b><small>Reviews</small></div></div>
  <div class="stat"><div class="ring"><svg width="22" height="22" viewBox="0 0 22 22"><path d="M11 19S3 13.5 3 8.2A4.2 4.2 0 0 1 11 6a4.2 4.2 0 0 1 8 2.2C19 13.5 11 19 11 19z" fill="#f6e78c"/></svg></div><div><b>GUEST</b><small>Favorite Staynest</small></div></div>
  <div class="stat"><div class="ring"><svg width="22" height="22" viewBox="0 0 22 22"><path d="M6 3h10v5a5 5 0 0 1-10 0z" fill="#f6e78c"/><path d="M6 5H3v2a3 3 0 0 0 3 3M16 5h3v2a3 3 0 0 1-3 3" fill="none" stroke="#f6e78c" stroke-width="1.4"/><rect x="10" y="13" width="2" height="4" fill="#f6e78c"/><rect x="7" y="17" width="8" height="2" fill="#f6e78c"/></svg></div><div><b>TOP 1%</b><small>of eligible Staynest homes</small></div></div>
</div>
<div class="abs cta cta-direct">BOOK DIRECT &amp; SAVE <svg width="9" height="9" viewBox="0 0 9 9"><path d="M1 8L8 1M3 1h5v5" fill="none" stroke="#1c1c1c" stroke-width="1.4"/></svg></div>
<div class="abs cta cta-avail">CHECK AVAILABILITY <svg width="9" height="9" viewBox="0 0 9 9"><path d="M1 8L8 1M3 1h5v5" fill="none" stroke="#fff" stroke-width="1.4"/></svg></div>

<!-- INTRO -->
<h2 class="abs intro-h2">BIRCH LANTERN RETREAT</h2>
<div class="abs q-photo-tr" role="img" aria-label="Backyard patio with fire pit and covered seating beside the house"></div>
<div class="abs q-photo-bl" role="img" aria-label="Open living room with sofas, fireplace and dining area"></div>
<div class="abs intro-copy">
  <p>A warm and inviting home in the heart of Bend, Oregon. Just a 5-minute walk to the Tannery Row Quarter with shops, restaurants, the Deschutes River, and the Larkspur Fields Pavilion.</p>
  <p>Relax in the private fenced backyard, cook in the well-equipped kitchen, gather by the fireplace, and enjoy everything Bend has to offer-all just steps away.</p>
</div>

<!-- COMFORT -->
<h2 class="abs sec-h2" style="top:1240px">DESIGNED FOR COMFORT</h2>
<div class="abs sec-script script" style="top:1280px">Made for Memories</div>
<div class="abs vline" style="top:1349px"></div>

<div class="abs yard-photo" role="img" aria-label="Green backyard with fire pit, blue Adirondack chairs and covered patio"></div>
<div class="abs yard-notch"></div>

<div class="card green" style="left:191px;top:1370px">
  <div class="ico"><svg width="28" height="28" viewBox="0 0 28 28"><path d="M14 3a7 7 0 0 0-7 7c0 5 7 14 7 14s7-9 7-14a7 7 0 0 0-7-7z" fill="#4d6530"/><circle cx="14" cy="10" r="2.6" fill="#bfe08f"/></svg></div>
  <h3>WALK TO<br>TANNERY ROW QUARTER</h3>
  <p>Shops, dining, river &amp; entertainment just minutes away.</p>
</div>
<div class="card olive" style="left:466px;top:1427px">
  <div class="ico"><svg width="28" height="28" viewBox="0 0 28 28"><circle cx="14" cy="18" r="5.5" fill="#fff"/><circle cx="6.5" cy="12" r="2.5" fill="#fff"/><circle cx="21.5" cy="12" r="2.5" fill="#fff"/><circle cx="10.5" cy="7" r="2.5" fill="#fff"/><circle cx="17.5" cy="7" r="2.5" fill="#fff"/></svg></div>
  <h3>PET<br>FRIENDLY</h3>
  <p>We welcome your four-legged family members.</p>
</div>
<div class="card green" style="left:738px;top:1370px">
  <div class="ico"><svg width="30" height="28" viewBox="0 0 30 28"><g fill="none" stroke="#4d6530" stroke-width="2"><path d="M4 24V8l2-3 2 3v16M11 24V8l2-3 2 3v16M18 24V8l2-3 2 3v16M25 24V8l-2-3-2 3"/><path d="M2 12h26M2 19h26"/></g></svg></div>
  <h3>PRIVATE<br>BACKYARD</h3>
  <p>Fenced yard with covered patio, seating &amp; fire pit.</p>
</div>
<div class="card olive" style="left:191px;top:1622px">
  <div class="ico"><svg width="30" height="26" viewBox="0 0 30 26"><path d="M4 18v-5l3-6h13l3 6v5z" fill="#fff"/><circle cx="9" cy="19" r="3" fill="#fff"/><circle cx="19" cy="19" r="3" fill="#fff"/><rect x="22" y="3" width="6" height="8" rx="1" fill="none" stroke="#fff" stroke-width="1.5"/></svg></div>
  <h3>EASY<br>PARKING</h3>
  <p>Off-street driveway parking for your convenience.</p>
</div>
<div class="card green" style="left:466px;top:1680px">
  <div class="ico"><svg width="30" height="26" viewBox="0 0 30 26"><g fill="none" stroke="#4d6530" stroke-width="2.4" stroke-linecap="round"><path d="M3 9a17 17 0 0 1 24 0M7 13.5a11 11 0 0 1 16 0M11 18a5 5 0 0 1 8 0"/></g><circle cx="15" cy="22" r="2" fill="#4d6530"/></svg></div>
  <h3>MODERN<br>COMFORTS</h3>
  <p>Fast WiFi, smart TV, AC, fireplace &amp; more for a perfect stay.</p>
</div>
<div class="card olive" style="left:738px;top:1622px">
  <div class="ico"><svg width="30" height="28" viewBox="0 0 30 28"><path d="M6 11h15v6a6 6 0 0 1-6 6h-3a6 6 0 0 1-6-6z" fill="#fff"/><path d="M21 13h2a3 3 0 0 1 0 6h-2" fill="none" stroke="#fff" stroke-width="1.8"/><rect x="4" y="24" width="20" height="1.8" fill="#fff"/><path d="M11 4c-1 2 1 3 0 5M15 4c-1 2 1 3 0 5" fill="none" stroke="#fff" stroke-width="1.4"/></svg></div>
  <h3>FULLY<br>EQUIPPED</h3>
  <p>Cook, dine &amp; relax in a kitchen with everything you need.</p>
</div>

<div class="abs gal" style="left:146px;background:linear-gradient(160deg,#e8e2d6,#b8a890 60%,#7a5e44)" role="img" aria-label="Bright kitchen with island and bar stools"></div>
<div class="abs gal" style="left:373px;background:linear-gradient(160deg,#e4dccb,#c4b093 55%,#7e6a4e)" role="img" aria-label="Bedroom with queen bed and ceiling fan"></div>
<div class="abs gal" style="left:603px;background:linear-gradient(180deg,#6f7f8a,#4d5a3c 45%,#8a7864)" role="img" aria-label="Stone patio with dining table under string lights at dusk"></div>
<div class="abs gal" style="left:831px;background:linear-gradient(160deg,#e6e0d4,#b9ab94 50%,#4a3728)" role="img" aria-label="Bathroom with double vanity and large mirror"></div>

<div class="abs vline" style="top:2757px"></div>

<!-- ADVENTURE -->
<div class="abs river-photo" role="img" aria-label="Aerial view of the Deschutes River winding past shops and trees at sunset"></div>
<h2 class="abs adv-h2">ADVENTURE<br>RELAXATION</h2>
<div class="abs adv-script script">Right Outside Your Door</div>
<p class="abs adv-copy">From the Tannery Row Quarter to mountain trails, Bend offers unforgettable experiences in every season.</p>
<div class="abs btn-explore">EXPLORE THE AREA <svg width="9" height="9" viewBox="0 0 9 9"><path d="M1 8L8 1M3 1h5v5" fill="none" stroke="#fff" stroke-width="1.4"/></svg></div>
<div class="abs spot" style="left:603px;background:linear-gradient(180deg,#8fa0b4,#c8b68c 30%,#5d7a3a 60%,#4b6a30)" role="img" aria-label="Outdoor pavilion lawn seating among trees"></div>
<div class="abs spot" style="left:831px;background:linear-gradient(170deg,#d8dde0,#8b8a80 40%,#9fb0b4 65%,#6f6a5c)" role="img" aria-label="Rushing Deschutes River over rocks"></div>
<div class="abs spot-cap" style="left:603px">LARKSPUR FIELDS<br>PAVILION<span>7 MIN WALK</span></div>
<div class="abs spot-cap" style="left:831px">DESCHUTES RIVER<span>7 MIN WALK</span></div>

<!-- REVIEWS -->
<h2 class="abs sec-h2" style="top:3584px;font-size:38px">WHAT OUR GUESTS<br>ARE SAYING</h2>
<svg class="abs arrow" style="left:172px" width="24" height="46" viewBox="0 0 24 46"><path d="M21 2L3 23l18 21" fill="none" stroke="#666" stroke-width="1.5"/></svg>
<svg class="abs arrow" style="left:990px" width="24" height="46" viewBox="0 0 24 46"><path d="M3 2l18 21L3 44" fill="none" stroke="#666" stroke-width="1.5"/></svg>

<div class="abs review" style="left:259px">
  <h4>George</h4>
  <div class="stars">★★★★★</div>
  <p>There are many variations of passages of Lorem Ipsum available, but the majority have suffered alteration in some form, by injected humour, or randomised words which don't look even slightly believable.</p>
  <p>If you are going to use a passage of Lorem Ipsum, you need to be sure there isn't anything.</p>
</div>
<div class="abs avatar" style="left:209px" role="img" aria-label="Guest portrait"></div>
<div class="abs review" style="left:650px">
  <h4>William</h4>
  <div class="stars">★★★★★</div>
  <p>Orci varius natoque penatibus et magnis dis parturient montes, nascetur ridiculus mus. Interdum et malesuada fames ac ante ipsum primis in faucibus. Sed justo lorem, posuere et porttitor id, viverra ut felis.</p>
  <p>Aliquam ut varius augue, sit amet placerat purus. Proin vulputate auctor nisl in vestibulum.</p>
</div>
<div class="abs avatar" style="left:600px;background:linear-gradient(135deg,#c9b8a4,#6b5a4a)" role="img" aria-label="Guest portrait"></div>

<!-- NEWSLETTER -->
<section class="abs news">
  <h2>STAY CONNECTED</h2>
  <div class="sub">Sign up for local tips and special offers.</div>
  <div class="abs field" style="left:296px;width:225px">NAME</div>
  <div class="abs field" style="left:528px;width:225px">EMAIL</div>
  <div class="abs btn-sub">SUBSCRIBE <svg width="9" height="9" viewBox="0 0 9 9"><path d="M1 8L8 1M3 1h5v5" fill="none" stroke="#fff" stroke-width="1.4"/></svg></div>
</section>

<!-- FOOTER -->
<footer class="abs footer">
  <nav>HOME<span>|</span>THE HOUSE<span>|</span>GALLERY<span>|</span>EXPLORE BEND<span>|</span>REVIEWS<span>|</span>FAQ<span>|</span>CONTACT</nav>
  <small>Copyright © 2026 Birch Lantern Retreat. All rights reserved.</small>
</footer>

</body>
</html>
```